ORLA - Óptica Médica - web design and concept

Website concept - Create and develop our website design and structure. ORLA is an optical store chain, and we are looking to establish our web and digital concept. In attachment there are several pictures about our stores and our logo.

The website structure should be user friendly. Colors should be light and the design as simple and minimalist as possible. There are different variations of the logothat can be used, check the file.

The website will include optical collections and sun collections as an online store. Also, a medical menu should be considered in order for clients to schedule optometry appointments. There should also be a menu for client assistance where the clients can read about glass maintenance in our workshop.
Updates

Low design quality

Number of Pages Required

5+ page

Font styles to use
Serif
Sans Serif

Requirements
Must have
• Must be user-friendly and minimalist.
• Please USE PICTURES FROM THE BRANDS we sell: MERUN, BOSKA, PNW, KOLE, BAMPE
Nice to have
• Nice to inspire: ZEK glasses (see website https://ch.shopzek.com/en/)
• Nice to inspire: https://merun-eyewear.com/
• Nice to ispire: https://www.pnwglobe.com/en/
Should not have
• Hysteric colors and shapes

```html
<!DOCTYPE html>
<html lang="en">
<head>
<meta charset="utf-8">
<title>ORLA Óptica Médica</title>
<link href="https://fonts.googleapis.com/css2?family=Crimson+Text:wght@400;600&family=Roboto:wght@400;500;700&display=swap" rel="stylesheet">
<style>
:root{
  --gold:#b3884b;
  --gold-dark:#9c7438;
  --ink:#1d1d1d;
  --text:#555;
  --header:#1c2129;
  --footer:#1f1f1f;
  --cream:#f5e8d2;
  --cream-light:#fbf8ef;
  --white:#fff;
  --red:#d0302c;
}
*{margin:0;padding:0;box-sizing:border-box}
html,body{width:1200px;height:3965px;overflow:hidden}
body{position:relative;background:var(--white);font-family:"Roboto",Arial,sans-serif;color:var(--text)}
.abs{position:absolute}
.btn{position:absolute;display:flex;align-items:center;justify-content:center;background:var(--gold);color:var(--white);font-family:"Roboto",sans-serif;font-weight:500;border-radius:30px}
.media{position:absolute}

/* header */
.site-header{position:absolute;left:0;top:0;width:1200px;height:98px;background:var(--header)}
.brand{position:absolute;left:88px;top:30px;display:flex;align-items:center;gap:10px;color:var(--gold);font-family:"Crimson Text",serif;font-size:30px;font-weight:600;letter-spacing:2px}
.brand-mark{width:12px;height:12px;background:var(--gold)}
.nav{position:absolute;top:38px;left:362px;color:var(--white);font-size:15px;font-weight:500}
.nav span{position:absolute;white-space:nowrap}
.trial{left:946px;top:29px;width:154px;height:37px;font-size:16px}

/* hero */
.hero{position:absolute;left:0;top:98px;width:1200px;height:457px;background:linear-gradient(100deg,#6f7680 0%,#4f5866 35%,#2f3b63 55%,#6a6e76 80%,#9c9c9a 100%)}
.hero-shade{position:absolute;inset:0;background:rgba(10,14,22,.35)}
.hero h1{position:absolute;left:0;width:1200px;top:92px;text-align:center;color:var(--white);font-family:"Crimson Text",serif;font-weight:600;font-size:56px;letter-spacing:1px}
.hero p{position:absolute;left:0;width:1200px;top:172px;text-align:center;color:var(--white);font-size:26px;line-height:43px}
.hero .contact{left:515px;top:285px;width:170px;height:45px;font-size:20px}
.dots{position:absolute;display:flex;gap:6px}
.dots i{width:10px;height:10px;border-radius:50%;border:1.5px solid var(--white);display:block}
.dots i.on{background:var(--white)}

/* section titles */
.section-title{position:absolute;left:0;width:1200px;text-align:center;font-family:"Crimson Text",serif;font-weight:400;color:var(--ink);font-size:42px;letter-spacing:1px}

/* about */
.about-title{position:absolute;left:608px;top:646px;font-family:"Crimson Text",serif;font-weight:400;font-size:44px;color:var(--ink);letter-spacing:1px}
.about-text{position:absolute;left:608px;top:716px;width:494px;font-size:13.5px;line-height:34px;color:var(--text)}
.read{left:608px;top:920px;width:132px;height:37px;font-size:13px}

/* guarantees */
.guarantees{position:absolute;left:0;top:1327px;width:1200px;height:478px;background:linear-gradient(180deg,#f3e2c6 0%,var(--cream) 45%,#f7ecd9 100%)}
.arrow{position:absolute;top:1550px}
.g-item{position:absolute;top:1535px}
.g-icon{position:absolute;left:0;top:0;width:60px;height:60px;border-radius:50%;background:#fbf4e8;display:flex;align-items:center;justify-content:center}
.g-title{position:absolute;left:80px;top:4px;width:240px;font-size:20px;color:var(--ink);line-height:29px}
.g-text{position:absolute;left:80px;width:260px;font-size:14px;line-height:34px;color:var(--ink)}

/* products */
.p-name{position:absolute;left:98px;top:1995px;font-size:25px;font-weight:700;color:var(--ink)}
.p-desc{position:absolute;left:98px;top:2043px;width:470px;font-size:14px;line-height:34px}
.stars{position:absolute;left:98px;top:2194px;color:var(--gold);font-size:14px;letter-spacing:1px}
.price{position:absolute;left:98px;top:2220px;color:var(--red);font-size:18px;font-weight:700}
.sq-btn{position:absolute;top:2260px;height:35px;display:flex;align-items:center;justify-content:center;font-size:14px}
.p-frame{position:absolute;left:630px;top:1998px;width:470px;height:294px;background:var(--white);box-shadow:0 2px 10px rgba(0,0,0,.15)}

/* brands */
.brands{position:absolute;left:0;top:2466px;width:1200px;height:354px;background:var(--cream-light)}
.brand-name{position:absolute;top:2668px;width:200px;text-align:center;color:#8a8a8a;font-family:"Crimson Text",serif;font-size:28px;letter-spacing:2px}

/* blog */
.card{position:absolute;top:3008px;width:278px;height:383px;background:var(--white);box-shadow:3px 4px 10px rgba(0,0,0,.25)}
.card .media{left:0;top:0;width:278px;height:169px}
.card p{position:absolute;left:20px;top:216px;width:238px;text-align:center;font-size:14px;line-height:27px;color:var(--text)}
.meta{position:absolute;left:0;top:322px;width:278px;display:flex;justify-content:center;align-items:center;gap:14px;font-size:12px;color:var(--gold)}
.meta span{display:flex;align-items:center;gap:5px}

/* footer */
.site-footer{position:absolute;left:0;top:3499px;width:1200px;height:466px;background:var(--footer)}
.f-head{position:absolute;top:3558px;font-family:"Crimson Text",serif;font-size:24px;font-weight:600;color:var(--white)}
.f-rule{position:absolute;top:3594px;height:1px;background:#4a4a4a}
.f-text{position:absolute;font-size:13.5px;line-height:35px;color:#d6d6d6}
.f-line{position:absolute;display:flex;align-items:flex-start;gap:16px;font-size:13.5px;line-height:33px;color:#d6d6d6}
.f-line svg{flex:none;margin-top:9px}
.f-links{position:absolute;left:954px;top:3622px;list-style:none;font-size:13.5px;line-height:34px;color:#d6d6d6}
.f-links li::before{content:"";display:inline-block;width:5px;height:5px;background:var(--gold);border-radius:50%;margin-right:18px;vertical-align:middle}
.book{left:100px;top:3859px;width:204px;height:40px;font-size:13px}
.copy{position:absolute;left:0;width:1200px;top:3932px;text-align:center;font-size:12px;color:#cfcfcf}
</style>
</head>
<body>

<header class="site-header">
  <div class="brand"><span class="brand-mark"></span>ORLA</div>
  <nav class="nav">
    <span style="left:0">Home</span>
    <span style="left:72px">About Us</span>
    <span style="left:162px">Products</span>
    <span style="left:250px">Contact</span>
    <span style="left:334px">Blog</span>
    <span style="left:396px">Store</span>
  </nav>
  <svg class="abs" style="left:822px;top:38px" width="18" height="18" viewBox="0 0 18 18"><circle cx="7.5" cy="7.5" r="5.5" fill="none" stroke="#fff" stroke-width="2"/><path d="M11.5 11.5l5 5" stroke="#fff" stroke-width="2.2"/></svg>
  <svg class="abs" style="left:878px;top:37px" width="20" height="18" viewBox="0 0 20 18"><path d="M1 2h3l2.5 9h10l2-7H5.5" fill="none" stroke="#fff" stroke-width="2"/><circle cx="8" cy="15" r="1.7" fill="#fff"/><circle cx="15" cy="15" r="1.7" fill="#fff"/></svg>
  <div class="btn trial">Get Free Trial</div>
</header>

<section class="hero">
  <div class="media" role="img" aria-label="Photo of the optical store interior with eyewear display shelves" style="inset:0"></div>
  <div class="hero-shade"></div>
  <h1>ORLA OPTICA MEDICA</h1>
  <p>We will be happy to help you and offer you the best solution<br>for your visual health problems.</p>
  <div class="btn contact">Contact Us</div>
  <div class="dots" style="left:571px;top:422px"><i class="on"></i><i></i><i></i><i></i></div>
</section>

<section class="about">
  <div class="media" role="img" aria-label="Photo of a store interior with wooden counter and pendant lamp" style="left:100px;top:658px;width:428px;height:566px;background:linear-gradient(180deg,#4a4640 0%,#6b5a44 45%,#c9c4bc 70%,#e2dfda 100%)"></div>
  <div class="media" role="img" aria-label="Photo of a smiling couple wearing sunglasses" style="left:550px;top:1023px;width:270px;height:201px;background:linear-gradient(135deg,#e8a24a 0%,#d88a5a 50%,#f1d3a4 100%)"></div>
  <div class="media" role="img" aria-label="Photo of a green contact lens case" style="left:846px;top:1023px;width:254px;height:201px;background:linear-gradient(135deg,#e4ece9 0%,#7fd0b4 55%,#cfe4de 100%)"></div>
  <h2 class="about-title">ABOUT US</h2>
  <p class="about-text">Lorem ipsum dolor sit amet, consectetur adipiscing elit, sed do eiusmod tempor incididunt ut labore et dolore magna aliqua. Ut enim ad minim veniam, quis trud exercitation ullamco laboris nisi ut aliquip ex ea commodo consequat. Duis aute irure dolor in reprehenderit in voluptate velit esse cillum dolore eu fugiat nulla pariatur.</p>
  <div class="btn read">READ MORE</div>
</section>

<section class="guarantees" role="img" aria-label="Soft warm background photo of the store"></section>
<h2 class="section-title" style="top:1418px">OUR GUARANTEES</h2>
<svg class="arrow" style="left:40px" width="14" height="24" viewBox="0 0 14 24"><path d="M12 2L3 12l9 10" fill="none" stroke="#111" stroke-width="3.5"/></svg>
<svg class="arrow" style="left:1142px" width="14" height="24" viewBox="0 0 14 24"><path d="M2 2l9 10-9 10" fill="none" stroke="#111" stroke-width="3.5"/></svg>

<div class="g-item" style="left:102px">
  <div class="g-icon"><svg width="26" height="30" viewBox="0 0 26 30"><circle cx="13" cy="7" r="5" fill="none" stroke="#a67d45" stroke-width="1.6"/><path d="M5 28v-8a8 8 0 0 1 16 0v8" fill="none" stroke="#a67d45" stroke-width="1.6"/></svg></div>
  <div class="g-title">Orla Childhood<br>Guarantee</div>
  <div class="g-text" style="top:64px">50% discount on new glasses,<br>if your child's graduation has<br>changed before six months.</div>
</div>
<div class="g-item" style="left:438px">
  <div class="g-icon"><svg width="34" height="24" viewBox="0 0 34 24"><rect x="2" y="4" width="30" height="16" rx="3" fill="none" stroke="#a67d45" stroke-width="1.6"/><circle cx="11" cy="12" r="4" fill="none" stroke="#a67d45" stroke-width="1.6"/><circle cx="23" cy="12" r="4" fill="none" stroke="#a67d45" stroke-width="1.6"/></svg></div>
  <div class="g-title">Orla Accident<br>Warranty</div>
  <div class="g-text" style="top:64px">Did you get off your glasses when<br>you got out of the car? Did your little<br>boy play with his sunglasses?</div>
</div>
<div class="g-item" style="left:810px">
  <div class="g-icon"><svg width="26" height="30" viewBox="0 0 26 30"><circle cx="13" cy="8" r="5" fill="none" stroke="#a67d45" stroke-width="1.6"/><path d="M4 28v-6a9 9 0 0 1 18 0v6M13 15v8" fill="none" stroke="#a67d45" stroke-width="1.6"/></svg></div>
  <div class="g-title">Orla Security</div>
  <div class="g-text" style="top:40px">If you have suffered a<br>robbery or robbery in your home,<br>you will opt for the replacement of<br>the same product at half price.</div>
</div>

<section class="products">
  <h2 class="section-title" style="top:1894px">PRODUCTS</h2>
  <h3 class="p-name">SUN GLASSES</h3>
  <p class="p-desc">Protect yourself adequately from ultraviolet (UV) rays thanks to our wide range of glasses, photochromic lenses and polarized lenses. Dress your look with the best quality and with prestigious brands: Marlo Vance, Teo Halvard, Vestra, Lumora, Cadenza ...</p>
  <div class="stars">★★★★★</div>
  <div class="price">$345.00</div>
  <div class="sq-btn" style="left:100px;width:111px;background:var(--gold-dark);color:#fff">Add To Cart</div>
  <div class="sq-btn" style="left:233px;width:111px;background:#ececec;color:#333">Buy Now</div>
  <div class="p-frame"></div>
  <div class="media" role="img" aria-label="Photo of mirrored sunglasses lying on sand" style="left:639px;top:2007px;width:452px;height:276px;background:linear-gradient(135deg,#cdbfa8 0%,#b9a98f 40%,#9a8d7a 60%,#d4c7b2 100%)"></div>
  <div class="dots" style="left:582px;top:2347px"><i class="on" style="border-color:var(--gold);background:var(--gold)"></i><i style="border-color:#999"></i><i style="border-color:#999"></i></div>
</section>

<section class="brands"></section>
<h2 class="section-title" style="top:2549px">OUR BRANDS</h2>
<div class="brand-name" style="left:72px">ALTEA</div>
<div class="brand-name" style="left:289px">FIORELLE</div>
<div class="brand-name" style="left:503px">NADIA ROUX</div>
<div class="brand-name" style="left:719px">VESTRA</div>
<div class="brand-name" style="left:939px">CADENZA</div>

<section class="blog">
  <h2 class="section-title" style="top:2908px">LATEST BLOG</h2>
  <article class="card" style="left:100px">
    <div class="media" role="img" aria-label="Blog cover photo about eyelid inflammation" style="background:linear-gradient(135deg,#8a7f74 0%,#c9c3bb 50%,#6f665e 100%)"></div>
    <p>Lorem ipsum dolor sit amet, consectetur adipiscing elit, sed do eiusmod tempor incididunt</p>
    <div class="meta"><span><svg width="12" height="11" viewBox="0 0 12 11"><path d="M1 1h10v6H5l-3 3V7H1z" fill="none" stroke="#b3884b" stroke-width="1.2"/></svg>10</span><span><svg width="11" height="11" viewBox="0 0 11 11"><circle cx="5.5" cy="5.5" r="4.5" fill="none" stroke="#b3884b" stroke-width="1.2"/><path d="M5.5 3v2.5l2 1.3" fill="none" stroke="#b3884b" stroke-width="1.2"/></svg>March 5,2017</span></div>
  </article>
  <article class="card" style="left:462px">
    <div class="media" role="img" aria-label="Blog cover photo about sunglasses for children" style="background:linear-gradient(135deg,#5a7fc7 0%,#b58ac0 50%,#d9c25a 100%)"></div>
    <p>Lorem ipsum dolor sit amet, consectetur adipiscing elit, sed do eiusmod tempor incididunt</p>
    <div class="meta"><span><svg width="12" height="11" viewBox="0 0 12 11"><path d="M1 1h10v6H5l-3 3V7H1z" fill="none" stroke="#b3884b" stroke-width="1.2"/></svg>10</span><span><svg width="11" height="11" viewBox="0 0 11 11"><circle cx="5.5" cy="5.5" r="4.5" fill="none" stroke="#b3884b" stroke-width="1.2"/><path d="M5.5 3v2.5l2 1.3" fill="none" stroke="#b3884b" stroke-width="1.2"/></svg>March 5,2017</span></div>
  </article>
  <article class="card" style="left:825px">
    <div class="media" role="img" aria-label="Blog cover photo about sun protection" style="background:linear-gradient(135deg,#5aa0d8 0%,#c94ba0 55%,#e5d53c 100%)"></div>
    <p>Lorem ipsum dolor sit amet, consectetur adipiscing elit, sed do eiusmod tempor incididunt</p>
    <div class="meta"><span><svg width="12" height="11" viewBox="0 0 12 11"><path d="M1 1h10v6H5l-3 3V7H1z" fill="none" stroke="#b3884b" stroke-width="1.2"/></svg>10</span><span><svg width="11" height="11" viewBox="0 0 11 11"><circle cx="5.5" cy="5.5" r="4.5" fill="none" stroke="#b3884b" stroke-width="1.2"/><path d="M5.5 3v2.5l2 1.3" fill="none" stroke="#b3884b" stroke-width="1.2"/></svg>March 5,2017</span></div>
  </article>
</section>

<footer class="site-footer"></footer>
<h4 class="f-head" style="left:100px">Who We Are</h4>
<div class="f-rule" style="left:100px;width:126px"></div>
<p class="f-text" style="left:100px;top:3622px;width:250px">ORLA OPTICA opens its doors with a clear purpose: to take care of you. Our priority is your visual health, and for this reason we have the best professionals and the most competitive products to serve your needs.</p>
<div class="btn book">BOOK AN APPOINTMENT</div>

<h4 class="f-head" style="left:389px">Contact Details</h4>
<div class="f-rule" style="left:389px;width:160px"></div>
<div class="f-line" style="left:382px;top:3622px"><svg width="14" height="16" viewBox="0 0 14 16"><path d="M7 15s5-5 5-9a5 5 0 0 0-10 0c0 4 5 9 5 9z" fill="none" stroke="#b3884b" stroke-width="1.4"/><circle cx="7" cy="6" r="1.8" fill="#b3884b"/></svg><span>Address Calle Molinos, 22. Norvella</span></div>
<div class="f-line" style="left:382px;top:3657px"><svg width="14" height="14" viewBox="0 0 14 14"><path d="M3 1l2 3-1.5 1.5a8 8 0 0 0 5 5L10 9l3 2-1.5 2.5C6 13 1 8 .5 2.5z" fill="none" stroke="#b3884b" stroke-width="1.3"/></svg><span>Telephone 900 11 22 33</span></div>
<div class="f-line" style="left:382px;top:3708px"><svg width="16" height="12" viewBox="0 0 16 12"><rect x="1" y="1" width="14" height="10" fill="none" stroke="#b3884b" stroke-width="1.3"/><path d="M1 1l7 6 7-6" fill="none" stroke="#b3884b" stroke-width="1.3"/></svg><span>hello@orlaoptica.example</span></div>

<h4 class="f-head" style="left:687px">Opening Hours</h4>
<div class="f-rule" style="left:687px;width:162px"></div>
<div class="f-line" style="left:680px;top:3622px"><svg width="16" height="16" viewBox="0 0 16 16"><circle cx="8" cy="8" r="6.5" fill="none" stroke="#b3884b" stroke-width="1.4"/><path d="M8 4v4l3 2" fill="none" stroke="#b3884b" stroke-width="1.4"/></svg><span>Monday - Friday: 10:00-14:00 &amp;<br>17:00-20:30<br>Saturday: 10:00 - 14:00</span></div>

<h4 class="f-head" style="left:954px">Quick Links</h4>
<div class="f-rule" style="left:954px;width:146px"></div>
<ul class="f-links">
  <li>Home</li><li>About Us</li><li>Products</li><li>Contact</li><li>Blog</li><li>Store</li>
</ul>
<div class="copy">© Copyrights 2018 Orlaoptica All Rights Reserved</div>

</body>
</html>
```